Upmarket Dessert Lounge needs a Business Card Design

We are an upmarket dessert lounge needing a business card to match our image.

We want something that is simple yet beautiful, feminine, classy, sophisticated and elegant. We want it to stand out and don't mind if it is bold.

The design should include our logo and colours of red or maroon with gold highlights. We don't mind if black is used.

Marlow & Quince

Target Market(s)

For those who like to indulge or treat themselves and give in to their temptations on good quality desserts.

Industry/Entity Type

Business

Requirements
Must have
• Must include our logo and our name

Marlow & Quince

M & Q

```html
<!DOCTYPE html>
<html lang="en">
<head>
<meta charset="utf-8">
<title>Marlow &amp; Quince — Business Card</title>
<link rel="stylesheet" href="https://fonts.googleapis.com/css2?family=PT+Sans:wght@400;700&family=Tinos:wght@400;700&display=swap">
<style>
  :root {
    --maroon: #7a1418;
    --maroon-deep: #651014;
    --gold: #f6d9a4;
    --white: #ffffff;
    --ink: #3a3a3a;
    --backdrop: #ece8e3;
  }
  * { box-sizing: border-box; margin: 0; padding: 0; }
  html, body { width: 1200px; height: 758px; overflow: hidden; }
  body {
    background: var(--backdrop);
    font-family: "PT Sans", Arial, sans-serif;
    position: relative;
  }
  .card {
    position: absolute;
    width: 500px;
    height: 286px;
    border-radius: 18px;
    overflow: hidden;
    box-shadow: 0 6px 18px rgba(0,0,0,.18);
  }
  /* Front */
  .card--front { left: 60px; top: 236px; background: var(--white); }
  .front__brand {
    position: absolute; top: 42px; left: 0; right: 0;
    display: flex; align-items: center; justify-content: center; gap: 10px;
    font-family: "Tinos", "Times New Roman", serif;
    font-size: 30px; color: var(--maroon); letter-spacing: .5px;
  }
  .front__brand-dot {
    width: 12px; height: 12px; border-radius: 50%; background: var(--maroon);
  }
  .front__band {
    position: absolute; left: 0; right: 0; top: 128px; height: 100px;
    background: var(--maroon);
    display: flex; align-items: center; justify-content: center;
    color: var(--white);
  }
  .front__address {
    text-align: right; font-size: 13px; line-height: 1.35;
    padding-right: 12px; margin-top: 18px;
  }
  .front__divider {
    width: 1px; height: 72px; background: rgba(255,255,255,.6);
  }
  .front__contacts { list-style: none; padding-left: 10px; font-size: 12.5px; line-height: 1.4; }
  .front__contacts li { display: flex; align-items: center; gap: 6px; }
  .front__contacts svg { width: 10px; height: 10px; fill: var(--white); flex: none; }
  .front__person {
    position: absolute; left: 0; right: 0; top: 240px;
    text-align: center; font-family: "Tinos", "Times New Roman", serif;
    font-size: 17px; color: var(--ink);
  }
  .front__person strong { font-weight: 700; }
  .front__person span { font-size: 14px; }
  /* Back */
  .card--back { left: 640px; top: 236px; background: var(--maroon); }
  .back__monogram {
    position: absolute; top: 62px; left: 0; right: 0; text-align: center;
    font-family: "Tinos", "Times New Roman", serif;
    font-size: 86px; color: var(--gold); line-height: 1;
  }
  .back__web {
    position: absolute; bottom: 42px; left: 0; right: 0; text-align: center;
    font-size: 20px; letter-spacing: 2.5px; color: var(--white);
  }
</style>
</head>
<body>
  <section class="card card--front" aria-label="Business card front">
    <div class="front__brand"><span class="front__brand-dot"></span>Marlow &amp; Quince</div>
    <div class="front__band">
      <p class="front__address">Street Name, City Name<br>State Zip Code</p>
      <span class="front__divider"></span>
      <ul class="front__contacts">
        <li><svg viewBox="0 0 10 10"><path d="M2 0h2l1 3-1.5 1a6 6 0 0 0 2.5 2.5L7 5l3 1v2a2 2 0 0 1-2 2A8 8 0 0 1 0 2a2 2 0 0 1 2-2z"/></svg>555-014-2870</li>
        <li><svg viewBox="0 0 10 10"><path d="M2.5 0h5a1 1 0 0 1 1 1v8a1 1 0 0 1-1 1h-5a1 1 0 0 1-1-1V1a1 1 0 0 1 1-1zm.5 1.5v6h4v-6z"/></svg>555-014-2870</li>
        <li><svg viewBox="0 0 10 10"><path d="M0 2h10v6H0zm1 .8 4 3 4-3z" fill-rule="evenodd"/></svg>hello@marlowquince.com</li>
        <li><svg viewBox="0 0 10 10"><circle cx="5" cy="5" r="4.5"/></svg>www.marlowquince.com</li>
      </ul>
    </div>
    <p class="front__person"><strong>Your name,</strong> <span>Title</span></p>
  </section>

  <section class="card card--back" aria-label="Business card back">
    <div class="back__monogram">M &amp; Q</div>
    <p class="back__web">www.marlowquince.com</p>
  </section>
</body>
</html>
```